Veldmark Supplies Business Card

Professional business card that stand out to our potential customers. Front and back with clean modern design

Industry/Entity Type

Oil and gas

Contact Information for Business Card

Name, address, website , office phone and cell number

Requirements
Must have
• Editable files for each employee

```html
<!DOCTYPE html>
<html lang="en">
<head>
<meta charset="UTF-8">
<title>Veldmark Supplies Business Card</title>
<link href="https://fonts.googleapis.com/css2?family=Poppins:wght@400;600&display=swap" rel="stylesheet">
<style>
  :root {
    --bg: #e3e6e8;
    --red: #e82127;
    --red-light: #f08a6a;
    --peach: #f3d2b8;
    --blue: #12b1d3;
    --ink: #1c1c1c;
    --white: #ffffff;
  }
  * { box-sizing: border-box; margin: 0; padding: 0; }
  html, body { width: 1200px; height: 960px; overflow: hidden; }
  body {
    background: var(--bg);
    font-family: "Poppins", Arial, sans-serif;
    position: relative;
  }
  .card {
    position: absolute;
    left: 249px;
    width: 702px;
    height: 400px;
    overflow: hidden;
  }
  .card-front { top: 60px; }
  .card-back { top: 500px; background: var(--white); }

  .front-pattern {
    position: absolute; inset: 0;
    background:
      radial-gradient(ellipse at 95% 5%, var(--peach) 0%, rgba(243,210,184,0) 55%),
      linear-gradient(135deg, var(--red) 0%, var(--red) 45%, var(--red-light) 100%);
  }

  .brand {
    position: absolute;
    left: 25px; top: 200px; width: 285px;
    display: flex; align-items: center; justify-content: center; gap: 10px;
  }
  .brand-mark { width: 22px; height: 22px; background: var(--red); flex: none; }
  .brand-name {
    font-weight: 600; font-size: 25px; color: var(--red);
    letter-spacing: 0.5px; white-space: nowrap;
  }

  .divider {
    position: absolute; left: 350px; top: 73px;
    width: 2px; height: 253px; background: var(--red);
  }

  .details { position: absolute; left: 406px; top: 80px; }
  .person-name {
    font-size: 33px; line-height: 40px; color: var(--red); font-weight: 400;
    white-space: nowrap;
  }
  .person-name strong { font-weight: 600; }
  .person-title { font-size: 17px; color: var(--blue); line-height: 24px; }
  .address {
    margin-top: 10px; font-size: 17px; line-height: 23px; color: var(--red);
  }
  .contact-list { list-style: none; margin-top: 14px; }
  .contact-list li {
    display: flex; align-items: center; gap: 10px;
    font-size: 18px; line-height: 23.5px; color: var(--ink);
  }
  .contact-list svg { width: 16px; height: 16px; flex: none; }

  .band { position: absolute; top: 355px; height: 25px; }
  .band-red { left: 0; width: 327px; background: var(--red); }
  .band-blue { left: 372px; right: 0; background: var(--blue); }
  .band-dot {
    position: absolute; left: 328px; top: 345px;
    width: 44px; height: 44px; border-radius: 50%;
    background: var(--white); border: 3px solid var(--red);
  }
</style>
</head>
<body>
  <section class="card card-front">
    <div class="front-pattern" role="img" aria-label="Repeating brand symbol pattern on red, fading to peach at the top right"></div>
  </section>

  <section class="card card-back">
    <div class="brand">
      <span class="brand-mark"></span>
      <span class="brand-name">Veldmark Supplies</span>
    </div>

    <div class="divider"></div>

    <div class="details">
      <h1 class="person-name"><strong>Marisol</strong> Vendrova</h1>
      <p class="person-title">Co-Founder &amp; CEO</p>
      <p class="address">418 Harlow Ridge Road,<br>Brookfield, WI 53005</p>
      <ul class="contact-list">
        <li>
          <svg viewBox="0 0 16 16"><path d="M3 1.5l2.5 0 1 3.5-1.6 1.2a8 8 0 0 0 4.9 4.9L11 9.5l3.5 1v2.5c0 1-1 1.5-2 1.5A11.5 11.5 0 0 1 1.5 3.5c0-1 .5-2 1.5-2z" fill="var(--blue)"/></svg>
          (817) 555-0142
        </li>
        <li>
          <svg viewBox="0 0 16 16"><rect x="4" y="1" width="8" height="14" rx="1.5" fill="none" stroke="var(--red)" stroke-width="1.6"/></svg>
          (555) 010-4471
        </li>
        <li>
          <svg viewBox="0 0 16 16"><circle cx="8" cy="8" r="7" fill="var(--blue)"/><path d="M4 5c2 0 2 2 4 2s1 3 0 4M10 3c0 2 2 2 3 3" stroke="var(--white)" stroke-width="1.3" fill="none"/></svg>
          www.veldmarksupply.com
        </li>
        <li>
          <svg viewBox="0 0 16 16"><rect x="1" y="5" width="14" height="10" fill="var(--red)"/><path d="M1 5l7 5 7-5" stroke="var(--white)" stroke-width="1.2" fill="none"/><rect x="4" y="1" width="8" height="6" fill="var(--white)" stroke="var(--red)" stroke-width="1"/></svg>
          info@veldmarksupply.com
        </li>
      </ul>
    </div>

    <div class="band band-red"></div>
    <div class="band band-blue"></div>
    <div class="band-dot"></div>
  </section>
</body>
</html>
```